Irrigation Business needs their business cards modernised and revamped

I would like to keep my current logo, colours and revamp the format of the card.

I would like the card to be clean yet important.

Im not sure if you include texture but i would like the named logo to be indented into the card etc.

show me something alive and free something thats clinical to the point yet has a feel of achievement. i would like people to go nice card.

Target Market(s)

high end clients, corporate, sports field manger, the guys that make the decisions

Industry/Entity Type

Business

Contact Information for Business Card

nformation to be included

Dean Harlow (Director)
0487305526
dean@kolvat.biz
www.kestonfieldworks.com

instagram logo
google logo
facebook logo

Colors

Designer to choose colors to be used in the design.

Requirements
Nice to have
• indentations a really nice feel to the card good texture

```html
<!DOCTYPE html>
<html lang="en">
<head>
<meta charset="utf-8">
<title>Keston Fieldworks – Business Card</title>
<link rel="stylesheet" href="https://fonts.googleapis.com/css2?family=Montserrat:wght@600;700&family=Open+Sans:wght@400;600&display=swap">
<style>
  :root {
    --bg: #2b2b2d;
    --card: #fbfbfb;
    --card-edge: #f1f1f1;
    --blue-deep: #2e6db4;
    --blue-mid: #3b7fc4;
    --blue-sky: #3fa9dc;
    --green: #3aaa5c;
    --ink: #4a4a4c;
  }
  * { margin: 0; padding: 0; box-sizing: border-box; }
  html, body { width: 1200px; height: 840px; overflow: hidden; }
  body {
    background: radial-gradient(ellipse at 50% 40%, #3a3a3c 0%, var(--bg) 70%);
    position: relative;
    font-family: "Open Sans", Arial, sans-serif;
  }
  .card {
    position: absolute;
    width: 540px;
    height: 310px;
    background: linear-gradient(160deg, var(--card) 0%, var(--card-edge) 100%);
    border-radius: 3px;
    box-shadow: 0 16px 34px rgba(0,0,0,.5);
    overflow: hidden;
  }
  .card--front { left: 90px; top: 100px; }
  .card--back { left: 570px; top: 420px; }

  /* front */
  .brand {
    position: absolute;
    left: 0; right: 0; top: 52px;
    display: flex; flex-direction: column; align-items: center;
  }
  .brand__mark {
    width: 86px; height: 86px; border-radius: 50%;
    background: linear-gradient(180deg, var(--blue-sky) 0%, var(--blue-deep) 100%);
  }
  .brand__name {
    margin-top: 18px;
    font-family: "Montserrat", Arial, sans-serif;
    font-weight: 700;
    font-size: 31px;
    line-height: 1.1;
    letter-spacing: .5px;
    text-align: center;
    color: var(--blue-mid);
  }
  .social {
    margin-top: 16px;
    display: flex; gap: 7px;
  }
  .social__item {
    width: 19px; height: 19px; border-radius: 50%;
    background: var(--blue-deep);
    box-shadow: inset 0 0 0 3px var(--blue-mid);
  }

  /* back */
  .contact {
    position: absolute;
    right: 24px; top: 26px;
    text-align: right;
  }
  .contact__name {
    font-family: "Montserrat", Arial, sans-serif;
    font-weight: 700; font-size: 15px;
    color: var(--blue-mid);
  }
  .contact__role {
    font-family: "Montserrat", Arial, sans-serif;
    font-weight: 600; font-size: 14px;
    color: var(--green);
    margin-bottom: 8px;
  }
  .contact__line {
    display: flex; justify-content: flex-end; align-items: center; gap: 7px;
    font-size: 13px; line-height: 19px;
    color: var(--ink);
  }
  .contact__icon { width: 11px; height: 11px; flex: none; }
  .feature {
    position: absolute;
    left: -90px; top: 120px;
    width: 360px; height: 360px;
  }
</style>
</head>
<body>

<section class="card card--front">
  <div class="brand">
    <span class="brand__mark"></span>
    <h1 class="brand__name">KESTON<br>FIELDWORKS</h1>
    <div class="social" aria-label="Social media">
      <span class="social__item"></span>
      <span class="social__item"></span>
      <span class="social__item"></span>
    </div>
  </div>
</section>

<section class="card card--back">
  <div class="contact">
    <p class="contact__name">DEAN HARLOW</p>
    <p class="contact__role">DIRECTOR</p>
    <p class="contact__line">0487305526
      <svg class="contact__icon" viewBox="0 0 12 12"><path fill="#2e6db4" d="M2.5 1h2l1 2.5-1.3 1a6 6 0 0 0 3.3 3.3l1-1.3L11 7.5v2A1.5 1.5 0 0 1 9.5 11 8.5 8.5 0 0 1 1 2.5 1.5 1.5 0 0 1 2.5 1z"/></svg>
    </p>
    <p class="contact__line">dean@kolvat.biz
      <svg class="contact__icon" viewBox="0 0 12 12"><rect x="1" y="2.5" width="10" height="7" rx="1" fill="#2e6db4"/><path d="M1.5 3l4.5 3.5L10.5 3" stroke="#fff" stroke-width="1" fill="none"/></svg>
    </p>
    <p class="contact__line">www.kestonfieldworks.com
      <svg class="contact__icon" viewBox="0 0 12 12"><circle cx="6" cy="6" r="5" fill="#2e6db4"/><path d="M1 6h10M6 1c2 2.5 2 7.5 0 10M6 1c-2 2.5-2 7.5 0 10" stroke="#fff" stroke-width=".8" fill="none"/></svg>
    </p>
  </div>
  <svg class="feature" viewBox="0 0 360 360" role="img" aria-label="Large brand emblem in blue tones">
    <defs>
      <linearGradient id="featureFill" x1="0" y1="0" x2="0" y2="1">
        <stop offset="0" stop-color="#3fa9dc"/>
        <stop offset="1" stop-color="#2e6db4"/>
      </linearGradient>
    </defs>
    <circle cx="180" cy="180" r="180" fill="url(#featureFill)"/>
  </svg>
</section>

</body>
</html>
```